Website - Loretta Dubrow

I need a website that has multiple pages and easy for me to update pictures, content and blogs as an ongoing basis’s.
It will have videos and needs to be compatible to view easily and aesthetically on mobile phones.
Please refer to this website for inspiration www.quinnafernsby.com

Coding

Coded - Design and coding required

Number of Pages Required

5+ page

Other font styles liked:
• Refer to website provided as inspiration

Requirements
Must have
• Please use stock images for now to do design, but I will be providing all imagery, videos and content

```html
<!DOCTYPE html>
<html lang="en">
<head>
<meta charset="utf-8">
<title>Loretta Dubrow</title>
<link rel="stylesheet" href="https://fonts.googleapis.com/css2?family=Sorts+Mill+Goudy&family=Mulish:wght@400;600;700&family=Yellowtail&display=swap">
<style>
:root{
  --sand:#ecdcc8;
  --accent:#e5b06d;
  --ink:#1d1d1d;
  --body:#7a6d60;
  --footer:#1f1e1e;
  --white:#ffffff;
}
*{margin:0;padding:0;box-sizing:border-box}
html,body{width:1200px;height:2909px;overflow:hidden}
body{position:relative;background:var(--sand);font-family:"Mulish",sans-serif;color:var(--ink)}
.abs{position:absolute}
/* hero */
.hero{left:0;top:0;width:1200px;height:612px;overflow:hidden}
.hero-panel{top:0;height:612px}
.panel-forest{left:0;width:397px;background:linear-gradient(170deg,#3d5a32 0%,#5b5f45 40%,#8a7b66 75%,#a59781 100%)}
.panel-sea{left:398px;width:401px;background:linear-gradient(180deg,#5b6b73 0%,#4d6670 30%,#7b6d63 60%,#5d4a3f 100%)}
.panel-rocks{left:800px;width:400px;background:linear-gradient(200deg,#4d4a48 0%,#7a6c62 45%,#a6917f 80%,#c5ae93 100%)}
.hero-shade{left:0;top:0;width:1200px;height:612px;background:rgba(20,20,20,.35)}
.hero-divider{top:0;width:2px;height:612px;background:#2a2a2a}
.logo{left:111px;top:26px;font-family:"Sorts Mill Goudy",serif;font-size:36px;color:var(--white)}
.nav{top:47px;font-size:14px;font-weight:700;color:var(--white);letter-spacing:.2px}
.nav.active{color:var(--accent)}
.btn{background:var(--accent);border-radius:26px;color:var(--ink);font-weight:700;font-size:14px;display:flex;align-items:center;justify-content:center}
.btn-start{left:935px;top:30px;width:152px;height:46px}
.motto{top:272px;font-family:"Yellowtail",cursive;font-size:44px;color:var(--white)}
.dot{top:574px;width:12px;height:12px;border-radius:50%;background:var(--white)}
/* about */
.about-frame{left:93px;top:720px;width:473px;height:379px;border:2px solid var(--ink)}
.about-photo{left:112px;top:707px;width:468px;height:373px;background:linear-gradient(160deg,#1c2a6b 0%,#202a55 40%,#2e7f6c 70%,#c7b9b0 100%)}
.heading{font-family:"Sorts Mill Goudy",serif;font-size:46px;color:var(--ink);font-weight:400}
.about-title{left:608px;top:698px}
.rule{height:2px;background:var(--ink)}
.about-text{left:608px;width:480px;font-size:13.5px;line-height:22.2px;color:var(--body);text-align:justify}
.btn-more{left:607px;top:1038px;width:154px;height:45px}
/* videos */
.video{top:1179px;width:384px;height:260px}
.video-1{left:9px;background:linear-gradient(120deg,#8a5a3c 0%,#c9c2b8 45%,#e8e6e2 100%)}
.video-2{left:406px;background:linear-gradient(180deg,#3a2340 0%,#5a2f4a 45%,#8a4c2e 75%,#3a2418 100%)}
.video-3{left:804px;background:linear-gradient(180deg,#3a2a2c 0%,#b9aea8 35%,#d7cfc9 65%,#3b3a3a 100%)}
.video-frame{left:15px;top:15px;right:15px;bottom:15px;border:2px solid var(--white)}
.play{left:173px;top:111px;width:38px;height:38px}
/* blog */
.blog-title{left:0;width:1200px;top:1520px;text-align:center}
.blog-photo{width:476px;height:287px}
.tone-1{background:linear-gradient(90deg,#8a5a40 0%,#c58c6d 45%,#8fc9d4 100%)}
.tone-2{background:linear-gradient(180deg,#9db3cf 0%,#4b5a48 30%,#7d94ae 55%,#d56ea8 100%)}
.tone-3{background:linear-gradient(160deg,#4a5348 0%,#9a6b4e 45%,#c88d70 70%,#a8a8a8 100%)}
.tone-4{background:linear-gradient(180deg,#e6e6e6 0%,#5a5a5a 40%,#9c9c9c 70%,#d8d8d8 100%)}
.post-title{width:476px;font-family:"Sorts Mill Goudy",serif;font-size:22px;line-height:34px;color:#3c3630}
.post-date{font-family:"Sorts Mill Goudy",serif;font-size:17px;color:#3c3630;display:flex;align-items:center;gap:5px}
/* footer */
.footer{left:0;top:2540px;width:1200px;height:369px;background:var(--footer)}
.foot-nav{left:0;top:2618px;width:1200px;display:flex;justify-content:center;align-items:center;gap:24px;color:var(--white);font-size:14px;font-weight:700}
.social{top:2663px;width:43px;height:43px;border-radius:50%;background:var(--sand)}
.foot-text{left:226px;top:2722px;width:748px;text-align:center;color:var(--white);font-size:12.5px;line-height:22.5px}
.foot-rule{left:112px;top:2817px;width:976px;height:1px;background:#8a8a8a}
.copyright{left:0;width:1200px;top:2850px;text-align:center;color:var(--white);font-size:13px}
</style>
</head>
<body>

<section class="hero abs">
  <div class="hero-panel panel-forest abs" role="img" aria-label="Woman in a red bikini sitting on a log beside a sun hat in a forest clearing"></div>
  <div class="hero-panel panel-sea abs" role="img" aria-label="Woman in a red swimsuit kneeling in the surf at dusk"></div>
  <div class="hero-panel panel-rocks abs" role="img" aria-label="Woman in a pink bikini standing among sandstone rocks"></div>
  <div class="hero-shade abs"></div>
  <div class="hero-divider abs" style="left:397px"></div>
  <div class="hero-divider abs" style="left:798px"></div>

  <div class="logo abs">Loretta Dubrow</div>
  <div class="nav active abs" style="left:446px">HOME</div>
  <div class="nav abs" style="left:538px">ABOUT</div>
  <div class="nav abs" style="left:634px">BLOG</div>
  <div class="nav abs" style="left:721px">VIDEOS</div>
  <div class="nav abs" style="left:821px">CONTACT</div>
  <div class="btn btn-start abs">GET STARTED</div>

  <div class="motto abs" style="left:310px">Be Bold</div>
  <div class="motto abs" style="left:517px">Be Brave</div>
  <div class="motto abs" style="left:737px">Be Yourself</div>

  <div class="dot abs" style="left:575px"></div>
  <div class="dot abs" style="left:594px"></div>
  <div class="dot abs" style="left:613px"></div>
</section>

<section class="about">
  <div class="about-frame abs"></div>
  <div class="about-photo abs" role="img" aria-label="Pageant winner with crown, sash and bouquet on stage"></div>
  <h2 class="heading about-title abs">About us</h2>
  <div class="rule abs" style="left:608px;top:752px;width:72px"></div>
  <p class="about-text abs" style="top:771px">Lorem ipsum dolor sit amet, consectetur adipiscing elit, sed do eiusmod tempor incididunt ut labore et dolore magna aliqua. Ut enim ad minim veniam, quis nostrud exercitation ullamco laboris nisi ut aliquip ex ea commodo cons equat. Duis aute irure dolor in reprehenderit in voluptate velit esse cillum dolore eu fugiat nulla pariatur. Excepteur sint occaecat cupidatat non proident, sunt in culpa qui officia deserunt mollit anim id est laborum.</p>
  <p class="about-text abs" style="top:949px">Lorem ipsum dolor sit amet, consectetur adipiscing elit, sed do eiusmod tempor incididunt ut labore et dolore magna aliqua. Ut enim ad minim veniam, quis nostrud exercitation</p>
  <div class="btn btn-more abs">LEARN MORE</div>
</section>

<section class="videos">
  <div class="video video-1 abs" role="img" aria-label="Dancer stretching in a bright studio">
    <svg class="play abs" viewBox="0 0 38 38"><circle cx="19" cy="19" r="19" fill="#e5b06d"/><path d="M14 10 L28 19 L14 28 Z" fill="#2a2a2a"/></svg>
  </div>
  <div class="video video-2 abs" role="img" aria-label="Dancer performing on a dim stage with warm lights">
    <div class="video-frame abs"></div>
    <svg class="play abs" viewBox="0 0 38 38"><circle cx="19" cy="19" r="19" fill="#e5b06d"/><path d="M14 10 L28 19 L14 28 Z" fill="#2a2a2a"/></svg>
  </div>
  <div class="video video-3 abs" role="img" aria-label="Group of dancers rehearsing in a studio">
    <svg class="play abs" viewBox="0 0 38 38"><circle cx="19" cy="19" r="19" fill="#e5b06d"/><path d="M14 10 L28 19 L14 28 Z" fill="#2a2a2a"/></svg>
  </div>
</section>

<section class="blog">
  <h2 class="heading blog-title abs">Latest Bolg</h2>
  <div class="rule abs" style="left:565px;top:1577px;width:71px"></div>

  <div class="blog-photo tone-1 abs" style="left:112px;top:1609px" role="img" aria-label="Portrait holding a smoothie against a blue wall"></div>
  <div class="post-title abs" style="left:112px;top:1907px">Lorem ipsum dolor sit amet, consectetur adipiscing consectetur adipiscing</div>
  <div class="post-date abs" style="left:110px;top:1987px"><svg width="16" height="16" viewBox="0 0 16 16"><rect x="1" y="3" width="14" height="12" fill="none" stroke="#3c3630" stroke-width="1.6"/><rect x="1" y="3" width="14" height="3" fill="#3c3630"/><path d="M4 1v3M12 1v3M4 9h2M8 9h2M12 9h1M4 12h2M8 12h2" stroke="#3c3630" stroke-width="1.6"/></svg>Aug 3, 2020</div>

  <div class="blog-photo tone-2 abs" style="left:612px;top:1609px" role="img" aria-label="Woman in pink dress on a jetty by the water"></div>
  <div class="post-title abs" style="left:613px;top:1907px">Lorem ipsum dolor sit amet, consectetur adipiscing consectetur adipiscing</div>
  <div class="post-date abs" style="left:611px;top:1987px"><svg width="16" height="16" viewBox="0 0 16 16"><rect x="1" y="3" width="14" height="12" fill="none" stroke="#3c3630" stroke-width="1.6"/><rect x="1" y="3" width="14" height="3" fill="#3c3630"/><path d="M4 1v3M12 1v3M4 9h2M8 9h2M12 9h1M4 12h2M8 12h2" stroke="#3c3630" stroke-width="1.6"/></svg>Aug 3, 2020</div>

  <div class="blog-photo tone-3 abs" style="left:112px;top:2046px" role="img" aria-label="Laughing woman with windswept hair on a boat"></div>
  <div class="post-title abs" style="left:112px;top:2344px">Lorem ipsum dolor sit amet, consectetur adipiscing consectetur adipiscing</div>
  <div class="post-date abs" style="left:110px;top:2424px"><svg width="16" height="16" viewBox="0 0 16 16"><rect x="1" y="3" width="14" height="12" fill="none" stroke="#3c3630" stroke-width="1.6"/><rect x="1" y="3" width="14" height="3" fill="#3c3630"/><path d="M4 1v3M12 1v3M4 9h2M8 9h2M12 9h1M4 12h2M8 12h2" stroke="#3c3630" stroke-width="1.6"/></svg>Aug 3, 2020</div>

  <div class="blog-photo tone-4 abs" style="left:612px;top:2046px" role="img" aria-label="Black and white portrait by a harbour"></div>
  <div class="post-title abs" style="left:613px;top:2344px">Lorem ipsum dolor sit amet, consectetur adipiscing consectetur adipiscing</div>
  <div class="post-date abs" style="left:611px;top:2424px"><svg width="16" height="16" viewBox="0 0 16 16"><rect x="1" y="3" width="14" height="12" fill="none" stroke="#3c3630" stroke-width="1.6"/><rect x="1" y="3" width="14" height="3" fill="#3c3630"/><path d="M4 1v3M12 1v3M4 9h2M8 9h2M12 9h1M4 12h2M8 12h2" stroke="#3c3630" stroke-width="1.6"/></svg>Aug 3, 2020</div>
</section>

<footer class="footer abs"></footer>
<nav class="foot-nav abs">
  <span>HOME</span><span>|</span><span>ABOUT</span><span>|</span><span>BLOG</span><span>|</span><span>VIDEOS</span><span>|</span><span>CONTACT</span>
</nav>
<div class="social abs" style="left:531px" aria-label="Social link"></div>
<div class="social abs" style="left:579px" aria-label="Social link"></div>
<div class="social abs" style="left:626px" aria-label="Social link"></div>
<p class="foot-text abs">Lorem ipsum dolor sit amet, consectetur adipiscing elit, sed do eiusmod tempor incididunt ut labore et dolore magna aliqua. Ut enim ad minim veniam, quis nostrud exercitation ullamco laboris nisi ut aliquip ex ea commodo consequat. Duis aute irure dolor in reprehenderit in voluptate velit esse cillum dolore</p>
<div class="foot-rule abs"></div>
<p class="copyright abs">© Copyrights 2021 Company name | All Reserved</p>

</body>
</html>
```